Tradlo - Forex Signal Services Moments Matter Most. Reshape your path.

I need an attractive eye catching web design that is azure friendly. I currently have a web programmer working on the backend of my website. Now I need a professional design to attract and retain customers. This site needs to be mobile friendly.

Tradlo is a highly reputable, trustworthy and professional site that offers forex signals to traders in all parts of the globe. With accurate and reliable forex signals, traders can not only make money but also boost their profits.

At Tradlo, we want our clients to have complete faith on us and our services! We also do not want our users to lead a simple and monotonous life. Instead our goal is to help them create an extra source of steady income. However, this is possible only when our clients resolve to change their lives for the better. They need to change their mindset and most importantly develop a positive frame of mind. That’s exactly why at Tradlo, we provide our clients with innumerable personal development tools and resources that’ll aid them in changing all the aspects of their lives. We want our traders to feel inspired and educate them in the right way!

Colors are flexible.

I do like the simplicity of www.brightmarkvo.example.
I do want a design more professional in appearance and not everything on page one.

I have not been able to decide on a logo. There is one of lower quality as I have not paid for it yet but I will if you decide it's the best for my business I will. Or should one feel that they have a better idea for a logo, I will pay for it if i like it.

I have included some of the content of my site so you can get a feel for where I am coming from.
(Please note that this content is still in the editing process)
Updates

Project Deadline Extended Reason: My content was not complete nor finalization of the final logo. We will allow a few more days for designers to modify the website.Thank you for your patience and understanding. Added Tuesday, January 24, 2017

Target Market(s)

I work with Forex Traders, Investors wanting to control their own portfolios, and remote nomads/mellienials

Coding

Coded - Design and coding required

Number of Pages Required

5+ page

Requirements
Must have
• I must have a professional clean look. I want the site to be interactive and eye catching. I want my audience hooked within seconds of opening it. It has to have all important information first. Photos must be legit and not spammy. I work as a representative in the financial market. I want my site to reflect that I stand by my product and reputation means everything to me. This site has to be engaging.
• Sorry, I should have included this earlier of what I will all need on this site.
• I'll have about Tradlo (my company, what we stand for, who we work with, my strategy, etc....
• about me (why i started this company, who I am)
• Performance (graphs and recent posts of signals)
• Membership (how to sign up)
• Terms of service/legal/disclaimers
• FAQS
• Personal Development Resources
• Forex Education Resources
Nice to have
• Quick links to bounce around the site faster.
Should not have
• I do not want over the top white collar conservative.

```html
<!DOCTYPE html>
<html lang="en">
<head>
<meta charset="utf-8">
<title>Tradlo - Forex Signal Services</title>
<link href="https://fonts.googleapis.com/css2?family=Open+Sans:wght@300;400;600&family=Oswald:wght@300;400&display=swap" rel="stylesheet">
<style>
:root{
  --red:#c4161c;
  --orange:#f0854b;
  --ink:#222;
  --body:#6b6b6b;
  --muted:#8a8a8a;
  --soft:#f3f3f3;
  --line:#d6d6d6;
  --white:#fff;
  --hero-a:#0f3b4c;
  --hero-b:#5a3a38;
  --hero-c:#c0602a;
}
*{margin:0;padding:0;box-sizing:border-box}
html,body{width:1200px;height:2612px;overflow:hidden;background:var(--white)}
body{font-family:"Open Sans",Arial,sans-serif;color:var(--ink);position:relative}

/* header */
.site-header{position:absolute;top:0;left:0;width:1200px;height:120px;background:var(--white)}
.brand{position:absolute;left:140px;top:36px;display:flex;align-items:center;gap:10px}
.brand-mark{width:30px;height:30px;border-radius:50%;background:var(--red)}
.brand-name{font-size:34px;font-weight:400;color:var(--ink);letter-spacing:1px;white-space:nowrap}
.main-nav{position:absolute;left:0;top:46px;width:1200px;height:36px}
.main-nav a{position:absolute;top:0;font-size:15.5px;color:#333;text-decoration:none;line-height:36px;white-space:nowrap}
.main-nav a.active{color:var(--orange);border:1.5px solid var(--orange);border-radius:20px;width:94px;text-align:center;line-height:33px}
.main-nav a.login{background:var(--red);color:var(--white);border-radius:20px;width:86px;text-align:center;line-height:34px}

/* hero */
.hero{position:absolute;top:120px;left:0;width:1200px;height:563px;
  background:linear-gradient(100deg,var(--hero-a) 0%,#1d4e5e 30%,var(--hero-b) 62%,var(--hero-c) 82%,#2a2a3a 100%)}
.hero-title{position:absolute;right:89px;top:284px;text-align:right;color:var(--white);font-family:"Oswald",Arial,sans-serif;white-space:nowrap}
.hero-title .l1{display:block;font-size:56px;font-weight:400;line-height:62px;letter-spacing:-.5px}
.hero-title .l2{display:block;font-size:43px;font-weight:300;line-height:52px;letter-spacing:.5px}
.hero-arrows{position:absolute;left:1050px;top:451px;display:flex;gap:10px}
.hero-arrows span{width:26px;height:26px;border-radius:50%;background:rgba(0,0,0,.45);display:flex;align-items:center;justify-content:center}

/* services */
.services{position:absolute;top:683px;left:0;width:1200px;height:461px;background:var(--soft)}
.section-title{font-size:31px;font-weight:400;color:var(--ink);text-align:center;letter-spacing:.5px}
.services .section-title{position:absolute;top:43px;width:100%}
.service{position:absolute;width:460px}
.service-icon{position:absolute;left:0;top:0;width:92px;height:92px;border:1.5px solid #333;border-radius:50%;display:flex;align-items:center;justify-content:center;background:var(--white)}
.service h3{position:absolute;left:111px;top:10px;font-size:17px;font-weight:400;color:#333;white-space:nowrap}
.service p{position:absolute;left:111px;top:38px;width:346px;font-size:12px;line-height:19px;color:var(--body)}

/* why */
.why{position:absolute;top:1144px;left:0;width:1200px;height:354px}
.why-copy{position:absolute;left:0;top:0;width:599px;height:354px;background:var(--orange);padding:52px 24px 0 89px;color:var(--white)}
.why-copy h2{font-size:26px;font-weight:600;letter-spacing:.5px;margin-bottom:10px}
.why-copy p{font-size:12.5px;line-height:20.5px;text-align:justify}
.btn-ghost{position:absolute;display:inline-block;border:1.5px solid currentColor;border-radius:20px;font-size:12.5px;line-height:34px;padding:0 19px;text-decoration:none;white-space:nowrap}
.why-copy .btn-ghost{left:89px;top:276px;color:var(--white)}
.why-photo{position:absolute;left:599px;top:0;width:601px;height:354px;background:linear-gradient(135deg,#d9c4a8 0%,#b58a62 40%,#e8e6e4 70%,#c9ccd2 100%)}

/* about */
.about{position:absolute;top:1498px;left:0;width:1200px;height:432px;background:var(--white)}
.video{position:absolute;left:91px;top:82px;width:512px;height:289px;border:1px solid var(--line);padding:4px;background:var(--white)}
.video-fill{width:100%;height:100%;background:linear-gradient(120deg,#8b7a66 0%,#c9b59a 45%,#6e6a66 100%);position:relative}
.play{position:absolute;left:50%;top:50%;width:64px;height:64px;margin:-32px 0 0 -32px;border-radius:50%;background:rgba(0,0,0,.55);display:flex;align-items:center;justify-content:center}
.about h2{position:absolute;left:636px;top:96px;font-size:26px;font-weight:400;color:var(--ink);letter-spacing:.3px;white-space:nowrap}
.about p{position:absolute;left:636px;top:142px;width:476px;font-size:13px;line-height:21px;color:var(--body);text-align:justify}
.about .btn-ghost{left:636px;top:313px;color:var(--red)}

/* blog */
.blog{position:absolute;top:1930px;left:0;width:1200px;height:400px;background:#efefef}
.blog .section-title{position:absolute;top:46px;width:100%}
.post{position:absolute;top:108px;width:310px;text-align:center}
.post-photo{width:310px;height:197px}
.post h3{font-size:15.5px;font-weight:400;color:#333;margin-top:14px;white-space:nowrap}
.post time{display:block;font-size:14px;color:#555;margin-top:2px}

/* footer */
.site-footer{position:absolute;top:2330px;left:0;width:1200px;height:282px;background:var(--white)}
.foot-brand{position:absolute;left:130px;top:78px;display:flex;flex-direction:column;align-items:center;gap:8px}
.foot-brand .brand-mark{width:40px;height:40px}
.foot-brand .brand-name{font-size:32px}
.foot-col{position:absolute;top:60px}
.foot-col h4{font-size:15px;font-weight:400;color:#333;margin-bottom:16px;letter-spacing:.3px;white-space:nowrap}
.foot-col p{font-size:11.5px;line-height:21px;color:var(--body);white-space:nowrap}
.subscribe{display:flex;margin-top:12px}
.subscribe span{width:147px;height:29px;border:1px solid #ccc;font-size:11.5px;color:#777;padding-left:7px;line-height:27px}
.subscribe b{width:57px;height:29px;background:var(--red);color:var(--white);font-size:12px;font-weight:400;line-height:29px;text-align:center}
.social{display:flex;gap:14px}
.social span{width:24px;height:24px;background:#666;border-radius:3px}
.foot-rule{position:absolute;left:91px;top:216px;width:1020px;height:1px;background:var(--line)}
.copyright{position:absolute;top:243px;width:100%;text-align:center;font-size:12.5px;color:#333}
</style>
</head>
<body>

<header class="site-header">
  <div class="brand"><span class="brand-mark"></span><span class="brand-name">Tradlo</span></div>
  <nav class="main-nav">
    <a class="active" href="#" style="left:336px">HOME</a>
    <a href="#" style="left:451px">ABOUT US</a>
    <a href="#" style="left:564px">SERVICES</a>
    <a href="#" style="left:677px">PROJECTS</a>
    <a href="#" style="left:789px">SUPPORT</a>
    <a href="#" style="left:900px">CONTACT US</a>
    <a class="login" href="#" style="left:1024px">LOGIN</a>
  </nav>
</header>

<section class="hero" role="img" aria-label="Businessman in a suit looking at a glowing forex chart wall">
  <h1 class="hero-title"><span class="l1">MOMENTS MATTER MOST</span><span class="l2">RESHAPE YOUR PATH</span></h1>
  <div class="hero-arrows">
    <span><svg width="10" height="12" viewBox="0 0 10 12"><path d="M7 1 2 6l5 5" fill="none" stroke="#fff" stroke-width="2"/></svg></span>
    <span><svg width="10" height="12" viewBox="0 0 10 12"><path d="M3 1l5 5-5 5" fill="none" stroke="#fff" stroke-width="2"/></svg></span>
  </div>
</section>

<section class="services">
  <h2 class="section-title">FOREX SIGNAL SERVICES</h2>

  <div class="service" style="left:92px;top:140px">
    <div class="service-icon"><svg width="42" height="36" viewBox="0 0 42 36"><circle cx="15" cy="20" r="9" fill="none" stroke="var(--red)" stroke-width="6" stroke-dasharray="4 3"/><circle cx="15" cy="20" r="3" fill="var(--red)"/><circle cx="31" cy="10" r="6" fill="none" stroke="var(--red)" stroke-width="4" stroke-dasharray="3 2"/><circle cx="32" cy="27" r="5" fill="none" stroke="var(--red)" stroke-width="3.5" stroke-dasharray="3 2"/></svg></div>
    <h3>OUR STRATEGY</h3>
    <p>We use proven strategies to help traders in succeeding in the forex market. Our forex experts provide high-probability, professional and consistent forex signals and charts</p>
  </div>

  <div class="service" style="left:653px;top:140px">
    <div class="service-icon"><svg width="38" height="34" viewBox="0 0 38 34"><rect x="1" y="1" width="36" height="24" rx="2" fill="var(--red)"/><rect x="15" y="25" width="8" height="5" fill="var(--red)"/><rect x="10" y="30" width="18" height="3" fill="var(--red)"/></svg></div>
    <h3>WHY US?</h3>
    <p>We use proven strategies to help traders in succeeding in the forex market. Our forex experts provide high-probability, professional and consistent forex signals and charts</p>
  </div>

  <div class="service" style="left:92px;top:286px">
    <div class="service-icon"><svg width="36" height="26" viewBox="0 0 36 26"><rect x="1" y="1" width="34" height="24" rx="2" fill="none" stroke="var(--red)" stroke-width="2.5"/><rect x="5" y="5" width="26" height="16" fill="var(--red)"/><circle cx="18" cy="13" r="5" fill="#fff"/><circle cx="18" cy="13" r="2" fill="var(--red)"/></svg></div>
    <h3>INVESTORS</h3>
    <p>We use proven strategies to help traders in succeeding in the forex market. Our forex experts provide high-probability, professional and consistent forex signals and charts</p>
  </div>

  <div class="service" style="left:653px;top:286px">
    <div class="service-icon"><svg width="32" height="38" viewBox="0 0 32 38"><rect x="2" y="2" width="18" height="24" fill="var(--red)"/><path d="M11 10h13l6 6v20H11z" fill="#fff" stroke="var(--red)" stroke-width="2.5"/><path d="M24 10v6h6" fill="none" stroke="var(--red)" stroke-width="2"/></svg></div>
    <h3>FOREX TRADERS</h3>
    <p>We use proven strategies to help traders in succeeding in the forex market. Our forex experts provide high-probability, professional and consistent forex signals and charts</p>
  </div>
</section>

<section class="why">
  <div class="why-copy">
    <h2>WHY TRADLO</h2>
    <p>We follow naked forex trading techniques including price action, immediate trend and personalized mathematical formulas. Our success stems from our strict enforcement of discipline, patience, attitude, economics and timing to help our traders maximize their gains from forex trading Obviously we do not always win, but our winning trades exceed those that are not and our take profit target is always bigger than our stop loss. We look at multiple time frames to qualify setups that define our trading edge. We pay close to the London market and our entries are often based off of the 1-hour chart.</p>
    <a class="btn-ghost" href="#">Read More »</a>
  </div>
  <div class="why-photo" role="img" aria-label="Trader at a laptop reviewing printed charts on a wooden table"></div>
</section>

<section class="about">
  <div class="video"><div class="video-fill" role="img" aria-label="Video still of colleagues meeting around an office table">
    <span class="play"><svg width="24" height="28" viewBox="0 0 24 28"><path d="M3 2l19 12L3 26z" fill="#fff"/></svg></span>
  </div></div>
  <h2>FOREX TRADERS EVERYWHERE</h2>
  <p>We're a small company based in the beautiful rockies, Canmore, Alberta, Canada with over 9 years of successful trading experience in the foreign exchange market. We decided to launch our service for two reasons; learning to trade is a difficult process that leaves many aspiring traders frustrated, and on top of that, there is no shortage of bad signal services that take advantage of these traders. Our aim is to help aspiring traders become profitable while they're learning to trade, and even if they do not have the time</p>
  <a class="btn-ghost" href="#">Read More »</a>
</section>

<section class="blog">
  <h2 class="section-title">OUR BLOG</h2>
  <article class="post" style="left:92px">
    <div class="post-photo" role="img" aria-label="Investor in a suit against a night city skyline" style="background:linear-gradient(120deg,#2a2a33,#5c5a66 50%,#1d2233)"></div>
    <h3>INVESTORS AND RETIREES</h3><time>19/11/17</time>
  </article>
  <article class="post" style="left:444px">
    <div class="post-photo" role="img" aria-label="Person working on a laptop in warm sunlight" style="background:linear-gradient(120deg,#3a2c22,#d9a45a 55%,#f2e2c4)"></div>
    <h3>WORK FROM HOME</h3><time>17/11/17</time>
  </article>
  <article class="post" style="left:796px">
    <div class="post-photo" role="img" aria-label="Hands using a tablet with financial graphics" style="background:linear-gradient(120deg,#1e4c7a,#7fa8cc 55%,#dbe6f0)"></div>
    <h3>YOU &nbsp;MAKE MONEY</h3><time>13/11/17</time>
  </article>
</section>

<footer class="site-footer">
  <div class="foot-brand"><span class="brand-mark"></span><span class="brand-name">Tradlo</span></div>
  <div class="foot-col" style="left:322px">
    <h4>CONTACT US</h4>
    <p>Address : 12 Harlow Lane, Eastgate<br>Norwick, NW4 7QT<br>Phone : +000 4 5550192<br>Email : hello@tradlo.example</p>
  </div>
  <div class="foot-col" style="left:637px">
    <h4>JOIN OUR MAILING LIST</h4>
    <p>Your about us information would fit<br>here nicely.</p>
    <div class="subscribe"><span>Email address</span><b>Submit</b></div>
  </div>
  <div class="foot-col" style="left:937px">
    <h4>FOLLOW US OUT THERE</h4>
    <div class="social"><span></span><span></span><span></span><span></span></div>
  </div>
  <div class="foot-rule"></div>
  <p class="copyright">Copyright © 2017. All Rights Reserved</p>
</footer>

</body>
</html>
```